A business card design for a dental office. We have Two doctors working here. We practice general de

I already have a logo designed for the office with the name and a slogan.
Now I need to create design for a business card using the same logo.
Details Needed on the front side of the card are :
Bernard K. Oswin, DDS
Gerald M Fenwick, DDS
418 Birch Lane
Portland, CT 00000
Phone : 555 019 4831
Fax : 555 019 4832
Website : WWW.BrightmoorToothHaven.Com
Office hours by appointment
On the back side of the card need :
Appointment
Date....................Time...................
With....................................
If unable to keep your appointment, please give 24-48 hours notice in order to avoid broken appointment fee.

Industry/Entity Type

Dental Clinic

Contact Information for Business Card

Bernard K. Oswin, DDS
Gerald M Fenwick, DDS
418 Birch Lane
Portland, CT 00000
Phone : 555 019 4831
Fax : 555 019 4832
Appointment

Requirements
Must have
• Keep the Name and slogan on the logo on the front of the card. You can move them around the Logo and Name/Slogan of business (Oswin Family Dentistry/We give you reasons to smile) as you wish to get a feel of the design.
• Bernard K. Oswin, DDS
• Gerald M Fenwick, DDS
• 418 Birch Lane
• Portland, CT 00000
• Phone : 555 019 4831
• Fax : 555 019 4832
• WWW.BrightmoorToothHaven.Com
• Keep these three groups above as they are together now in different areas of the front side.
• On the back side of the card need :
• Appointment
• Date....................Time...................
• With....................................
• If unable to keep your appointment, please give 24-48 hours notice in order to avoid broken appointment fee.

```html
<!DOCTYPE html>
<html lang="en">
<head>
<meta charset="utf-8">
<title>Oswin Family Dentistry – Business Card</title>
<link rel="stylesheet" href="https://fonts.googleapis.com/css2?family=Michroma&family=Arimo:wght@400;700&display=swap">
<style>
  :root {
    --bg: #e9e7e3;
    --paper: #f7f7f7;
    --blue: #1565c0;
    --blue-deep: #0d4fa3;
    --blue-light: #1e7fd6;
    --red: #e2203a;
    --white: #ffffff;
    --ink: #333333;
    --faint: #f3e0e2;
  }
  * { box-sizing: border-box; margin: 0; padding: 0; }
  html, body { width: 1200px; height: 892px; overflow: hidden; }
  body {
    background: var(--bg);
    display: flex;
    align-items: center;
    justify-content: center;
    gap: 40px;
    font-family: "Arimo", Arial, sans-serif;
  }
  .card {
    position: relative;
    width: 560px;
    height: 320px;
    background: var(--paper);
    overflow: hidden;
    box-shadow: 0 6px 18px rgba(0,0,0,.18);
  }

  /* Front */
  .front-top {
    position: absolute; left: 0; top: 0; right: 0; height: 142px;
    display: flex; align-items: center; padding: 0 24px; gap: 14px;
  }
  .brand-mark {
    display: flex; align-items: center; gap: 8px; flex: none;
    font-family: "Arimo", Arial, sans-serif; font-weight: 700;
    font-size: 19px; color: var(--blue);
  }
  .brand-mark .dot {
    width: 56px; height: 56px; border-radius: 50%; background: var(--blue);
  }
  .title-block { text-align: center; flex: 1; min-width: 0; }
  .practice-name {
    font-family: "Michroma", sans-serif; font-weight: 400; font-size: 15px; color: var(--blue);
    letter-spacing: 0.5px; text-transform: uppercase; white-space: nowrap;
  }
  .slogan {
    margin-top: 8px; display: flex; align-items: center; justify-content: center; gap: 8px;
    font-family: "Michroma", sans-serif; font-size: 7.5px; color: var(--red);
    letter-spacing: 1.5px; text-transform: uppercase; white-space: nowrap;
  }
  .slogan::before, .slogan::after {
    content: ""; width: 26px; height: 1px; background: var(--red);
  }
  .front-band {
    position: absolute; left: 0; right: 0; top: 146px; bottom: 0;
    background: linear-gradient(160deg, var(--blue-light), var(--blue-deep));
    border-top: 4px solid var(--red);
    display: flex; align-items: center; padding: 0 24px;
  }
  .doctors { width: 232px; flex: none; }
  .doctor { font-weight: 700; text-transform: uppercase; font-size: 18px; line-height: 1.1; }
  .doctor .cred { display: block; font-size: 14px; }
  .doctor--lead { color: var(--red); margin-bottom: 14px; }
  .doctor--second { color: var(--white); }
  .contacts {
    border-left: 1.5px solid var(--white); padding-left: 16px;
    color: var(--white); font-size: 14px; list-style: none; white-space: nowrap;
  }
  .contacts li { display: flex; align-items: center; gap: 9px; line-height: 1.85; }
  .contacts svg { width: 13px; height: 13px; flex: none; }

  /* Back */
  .back-band { position: absolute; left: 0; top: 0; width: 100%; height: 110px; }
  .back-band svg { display: block; }
  .appointment-title {
    position: absolute; left: 0; right: 0; top: 26px; text-align: center;
    font-family: "Arimo", Arial, sans-serif; font-weight: 700; font-size: 36px;
    letter-spacing: 2px; text-transform: uppercase; color: var(--white);
  }
  .faint-name {
    position: absolute; right: 34px; bottom: 8px;
    font-family: "Arimo", Arial, sans-serif; font-weight: 700; font-size: 56px;
    line-height: 1; color: var(--faint);
  }
  .appointment-rows {
    position: absolute; left: 40px; right: 40px; top: 134px; list-style: none;
    color: var(--ink); font-size: 17px; font-style: italic;
  }
  .appointment-rows li { display: flex; align-items: baseline; gap: 6px; margin-bottom: 24px; }
  .appointment-rows .fill { flex: 1; border-bottom: 2px dotted var(--ink); }
</style>
</head>
<body>

<section class="card card--front" aria-label="Card front">
  <div class="front-top">
    <div class="brand-mark"><span class="dot"></span>Oswin</div>
    <div class="title-block">
      <h1 class="practice-name">Oswin Family Dentistry</h1>
      <p class="slogan">We give you reasons to smile</p>
    </div>
  </div>
  <div class="front-band">
    <div class="doctors">
      <p class="doctor doctor--lead">Bernard K. Oswin<span class="cred">DDS</span></p>
      <p class="doctor doctor--second">Gerald M Fenwick<span class="cred">DDS</span></p>
    </div>
    <ul class="contacts">
      <li><svg viewBox="0 0 16 16"><rect width="16" height="16" rx="2" fill="#fff"/><path d="M4 3l2 0 1 3-1.5 1a6 6 0 0 0 3.5 3.5L10 9l3 1v2a1 1 0 0 1-1 1A9 9 0 0 1 3 4a1 1 0 0 1 1-1z" fill="#1565c0"/></svg>555 019 4831</li>
      <li><svg viewBox="0 0 16 16"><rect width="16" height="16" rx="2" fill="#fff"/><rect x="3" y="6" width="10" height="6" fill="#1565c0"/><rect x="5" y="3" width="6" height="3" fill="#1565c0"/></svg>555 019 4832</li>
      <li><svg viewBox="0 0 16 16"><rect width="16" height="16" rx="2" fill="#fff"/><circle cx="8" cy="8" r="4.5" fill="none" stroke="#1565c0" stroke-width="1.5"/><path d="M3.5 8h9M8 3.5v9" stroke="#1565c0" stroke-width="1.2"/></svg>WWW.BrightmoorToothHaven.Com</li>
      <li><svg viewBox="0 0 16 16"><rect width="16" height="16" rx="2" fill="#fff"/><path d="M8 3a3.5 3.5 0 0 1 3.5 3.5C11.5 9 8 13 8 13S4.5 9 4.5 6.5A3.5 3.5 0 0 1 8 3z" fill="#1565c0"/></svg>418 Birch Lane Portland, CT 00000</li>
    </ul>
  </div>
</section>

<section class="card card--back" aria-label="Card back">
  <div class="faint-name">Oswin</div>
  <div class="back-band">
    <svg width="560" height="110" viewBox="0 0 560 110">
      <defs>
        <linearGradient id="bandShade" x1="0" y1="0" x2="0" y2="1">
          <stop offset="0" stop-color="#1e7fd6"/>
          <stop offset="1" stop-color="#0d4fa3"/>
        </linearGradient>
      </defs>
      <path d="M0 0H560V78Q280 112 0 78Z" fill="url(#bandShade)"/>
      <path d="M0 80Q280 114 560 80" fill="none" stroke="#e2203a" stroke-width="4"/>
    </svg>
  </div>
  <h2 class="appointment-title">Appointment</h2>
  <ul class="appointment-rows">
    <li>Date<span class="fill"></span>Time<span class="fill"></span></li>
    <li>With<span class="fill"></span></li>
    <li>Date<span class="fill"></span>Time<span class="fill"></span></li>
  </ul>
</section>

</body>
</html>
```